Pebblebrook Plots - Online-only garden installation company

Online-only garden installation company. Our demographic is middle aged / suburban women, and we anticipate Facebook driving traffic to this website, as well as referrals from garden centers. The website must be very simple in design and function.

All orders will be placed through the website, including size of garden (3 options), location in yard, payment, and scheduling of installation date.

The website should employ a 3 step process:

Step 1: Select garden size. Either an 4' X 4', 8' X 4', or 12' X 4'.

Step 2: Select a location. We would like to use google maps to look up a US address, then "drag and drop" one of the garden sizes from step 1 to the location the customer would like us to install the garden at their home.

Step 3: Pick an installation date and pay. Using an online calendar the customer will pick a date, and then pay for the installation via credit card.

The website will be linked to an email account, PebblebrookPlots@mailvale.com to inform us of orders placed.

Target Market(s)

Our demographic is middle aged / suburban women, and we anticipate Facebook driving traffic to this website, as well as referrals from garden centers.

Industry/Entity Type

Coding

Number of Pages Required

Requirements
Must have
• Scheduling and payment options.

```html
<!DOCTYPE html>
<html lang="en">
<head>
<meta charset="utf-8">
<title>Pebblebrook Plots</title>
<link href="https://fonts.googleapis.com/css2?family=Lato:wght@400;700;900&display=swap" rel="stylesheet">
<style>
:root{
  --green:#10a24b;
  --green-dark:#0b8a3e;
  --mint:#e7f8ee;
  --mint-alt:#f2fcf6;
  --charcoal:#3b3b3b;
  --charcoal-deep:#2e2e2e;
  --orange:#e2581f;
  --text:#555;
  --beige:#e7ddcc;
  --white:#fff;
}
*{box-sizing:border-box;margin:0;padding:0}
html,body{width:1200px;height:3333px;overflow:hidden}
body{font-family:"Lato",sans-serif;color:var(--text);background:var(--white);position:relative}
.abs{position:absolute}
section,header,footer,nav,.bottombar{position:absolute;left:0;width:1200px}

/* top bar */
.topbar{top:0;height:107px;background:var(--charcoal)}
.call{left:733px;top:17px;color:var(--white);font-size:15px;display:flex;align-items:center;gap:10px;white-space:nowrap}
.icon-ring{width:26px;height:26px;border:2px solid var(--green);border-radius:50%;display:flex;align-items:center;justify-content:center}
.quote-outline{left:933px;top:16px;width:134px;height:28px;border:2px solid var(--green);color:var(--green);font-size:11px;font-weight:700;display:flex;align-items:center;justify-content:center;gap:8px;letter-spacing:.5px}
.follow{left:851px;top:64px;color:var(--white);font-size:14px;letter-spacing:.5px;display:flex;align-items:center;gap:8px;white-space:nowrap}
.social-dot{width:24px;height:24px;border:2px solid var(--white);border-radius:50%;display:inline-block}
.brand{left:122px;top:0;width:185px;height:167px;background:var(--white);z-index:5;display:flex;flex-direction:column;align-items:center;justify-content:center;gap:12px;box-shadow:0 2px 6px rgba(0,0,0,.2)}
.brand-dot{width:46px;height:46px;border-radius:50%;background:var(--green)}
.brand-name{font-size:19px;font-weight:900;color:var(--charcoal);text-align:center;line-height:1.1}

/* nav */
.nav{top:107px;height:60px;background:var(--green)}
.nav ul{list-style:none;position:absolute;right:130px;top:0;height:60px;display:flex;align-items:center}
.nav li{color:var(--white);font-size:15px;font-weight:700;letter-spacing:.5px;padding:0 36px;border-left:1px solid rgba(255,255,255,.6);line-height:22px}
.nav li:first-child{border-left:none}
.nav li:last-child{padding-right:0}

/* hero */
.hero{top:167px;height:522px;background:linear-gradient(180deg,#5f8d3a 0%,#7aa64a 25%,#b5743e 55%,#d38a4e 70%,#6b4f37 100%)}
.hero-banner{left:0;top:162px;width:500px;height:164px;background:rgba(16,162,75,.78);padding:22px 0 0 122px}
.hero-banner h1{color:var(--white);font-size:30px;font-weight:700;line-height:1.25;letter-spacing:.5px}
.btn-quote{display:inline-flex;align-items:center;gap:14px;margin-top:18px;background:var(--white);color:var(--charcoal);font-size:15px;font-weight:700;padding:9px 14px 9px 24px;letter-spacing:.5px}
.dots{left:545px;top:480px;display:flex;gap:12px}
.dots span{width:18px;height:18px;border-radius:50%;background:var(--white)}
.dots span:first-child{background:rgba(255,255,255,.45)}

/* services */
.services{top:689px;height:395px;background:var(--mint)}
.service{top:0;width:238px;height:395px;text-align:center}
.service:nth-child(odd){background:var(--mint-alt)}
.service .thumb{width:133px;height:133px;border-radius:50%;border:5px solid #cfeedd;margin:27px auto 0}
.service h3{font-size:18px;font-weight:700;color:var(--charcoal);letter-spacing:1px;margin-top:34px}
.leaf-rule{display:block;margin:6px auto 0}
.service p{font-size:13px;line-height:18px;color:var(--text);padding:0 22px;margin-top:10px}
.read-more{display:inline-flex;align-items:center;gap:10px;margin-top:24px;border:2px solid var(--charcoal);padding:4px 8px 4px 14px;font-size:11px;font-weight:900;color:var(--charcoal);letter-spacing:.5px}

/* welcome */
.welcome{top:1084px;height:472px;background:linear-gradient(180deg,#3e8e2c 0%,#5aa636 45%,#6d9d49 62%,#9b9a8c 75%,#bdb4a2 88%,#d9cfbd 100%)}
.welcome-card{left:122px;top:67px;width:949px;height:249px;background:var(--white);text-align:center;padding:40px 60px 0}
.welcome-card h2{color:var(--orange);font-size:25px;font-weight:700;letter-spacing:.5px}
.welcome-card p{font-size:13px;line-height:23px;margin-top:14px;color:var(--text)}

/* projects */
.projects{top:1556px;height:400px;background:var(--beige)}
.section-title{text-align:center;font-size:25px;font-weight:700;color:var(--orange);letter-spacing:.5px}
.projects .section-title{position:absolute;top:36px;width:100%}
.projects .leaf-rule{position:absolute;left:522px;top:78px}
.proj{top:155px;width:173px;height:173px;border:4px solid var(--white)}
.feature-card{left:504px;top:133px;width:185px;height:213px;background:var(--white);text-align:center;font-size:16px;color:var(--charcoal)}
.feature-card .date{margin-top:8px}
.feature-card .proj-img{width:173px;height:150px;margin:6px auto 0}
.feature-card .meta{display:flex;justify-content:center;gap:16px;margin-top:6px;font-size:14px;font-weight:700;align-items:center}
.arrow-box{top:222px;width:34px;height:34px;border:2px solid #9a8f78;display:flex;align-items:center;justify-content:center;background:var(--beige)}

/* three step */
.steps{top:1956px;height:611px;background:linear-gradient(90deg,#4b5b3a 0%,#6f7d5c 20%,#3e6b2d 50%,#6a8d45 80%,#8aa86a 100%)}
.steps-head{left:93px;top:40px;width:1018px;height:82px;background:var(--white);border-radius:10px 10px 0 0;text-align:center;padding-top:20px}
.steps-head .leaf-rule{margin-top:4px}
.notch{left:150px;top:122px;width:0;height:0;border-left:17px solid transparent;border-right:17px solid transparent;border-top:16px solid var(--white);z-index:3}
.steps-panel{left:93px;top:122px;width:1018px;height:451px;background:var(--green)}
.step-label{color:var(--white);font-size:19px;font-weight:700;position:absolute;left:25px}
.field{position:absolute;left:25px;width:349px;height:45px;background:#dcd6c4;border:1px solid #c9c2ac;display:flex;align-items:center;padding-left:14px;font-size:13px;color:#888}
.field .addon{position:absolute;right:0;top:0;width:45px;height:43px;display:flex;align-items:center;justify-content:center}
.btn-white{position:absolute;background:var(--white);color:var(--green);font-size:15px;font-weight:700;display:flex;align-items:center;justify-content:center;border-radius:3px}
.calendar{left:378px;top:184px;width:129px;height:120px;background:var(--white);font-size:7px;color:#444;padding:3px}
.calendar table{width:100%;border-collapse:collapse;text-align:center}
.calendar td,.calendar th{height:14px;font-weight:400}
.calendar .sel{background:#2e6fb8;color:#fff}
.pay-row{position:absolute;left:25px;top:333px;display:flex;align-items:center;gap:6px}
.radio{width:16px;height:16px;border-radius:50%;border:2px solid var(--white);background:var(--white);box-shadow:inset 0 0 0 3px var(--green)}
.radio.off{box-shadow:none}
.card-chip{width:46px;height:30px;background:var(--white);border-radius:3px}
.map{left:529px;top:33px;width:449px;height:382px;background:linear-gradient(135deg,#e8e6e0 0%,#dedbd2 50%,#e9e7e1 100%)}

/* tips */
.tips{top:2567px;height:300px;background:var(--white)}
.tips h2{position:absolute;left:189px;top:50px;font-size:19px;font-weight:900;color:var(--green);letter-spacing:.5px}
.tips h2 span{color:var(--charcoal)}
.tip{position:absolute;left:193px;display:flex;gap:18px}
.tip .tip-img{width:129px;height:78px;flex:none}
.tip h4{font-size:13px;color:var(--green);font-weight:700}
.tip .date{font-size:11px;font-weight:700;color:var(--charcoal);margin-top:4px}
.tip p{font-size:11px;line-height:14px;margin-top:4px;width:250px}
.tip p b{color:var(--green)}
.newsletter{left:733px;top:71px;width:278px;height:206px;background:var(--green);padding:8px}
.newsletter .inner{border:2px solid var(--white);height:100%;text-align:center;padding-top:20px}
.newsletter h3{color:var(--white);font-size:19px;font-weight:700}
.newsletter .input{width:235px;height:22px;margin:0 auto;background:var(--white);font-size:10px;color:#777;text-align:left;padding:5px 8px}
.submit{left:827px;top:260px;width:91px;height:28px;background:var(--green);border:2px solid var(--white);border-radius:14px;color:var(--white);font-size:11px;font-weight:900;display:flex;align-items:center;justify-content:center;gap:6px}

/* skyline band */
.skyline{top:2867px;height:166px;background:linear-gradient(180deg,#ffffff 0%,#dbeaf6 45%,#b9d3e8 70%,#2f2f2f 88%,#2f2f2f 100%)}

/* footer */
.footer{top:3033px;height:256px;background:var(--charcoal)}
.footer h5{color:var(--white);font-size:15px;font-weight:700;letter-spacing:1px}
.fcol{position:absolute;top:47px}
.fcol ul{list-style:none;margin-top:38px}
.fcol li{color:var(--white);font-size:15px;font-weight:700;height:28.5px}
.fcol li::before{content:"›";margin-right:7px}
.contact-line{display:flex;gap:10px;color:var(--white);font-size:15px;font-weight:700;line-height:27px}
.foot-brand{left:884px;top:40px;width:187px;height:167px;background:#7a7a7a;display:flex;flex-direction:column;align-items:center;justify-content:center;gap:12px}
.foot-brand .brand-name{color:var(--charcoal)}
.bottombar{top:3289px;height:44px;background:var(--charcoal-deep);color:var(--white);font-size:13px;font-weight:700}
.bottombar .links{left:460px;top:14px;display:flex;gap:14px}
.bottombar .links span+span{border-left:1px solid #fff;padding-left:14px}
.bottombar .socials{left:978px;top:12px;display:flex;gap:4px}
.bottombar .social-dot{width:20px;height:20px;border:1px solid #bbb}
</style>
</head>
<body>

<header class="topbar">
  <div class="abs call"><span class="icon-ring"><svg width="12" height="12" viewBox="0 0 24 24"><path fill="#10a24b" d="M6.6 10.8a15 15 0 0 0 6.6 6.6l2.2-2.2c.3-.3.7-.4 1-.2 1.1.4 2.3.6 3.6.6.6 0 1 .4 1 1V20c0 .6-.4 1-1 1A17 17 0 0 1 3 4c0-.6.4-1 1-1h3.5c.6 0 1 .4 1 1 0 1.3.2 2.5.6 3.6.1.3 0 .7-.2 1z"/></svg></span>Call: 123-456-7890</div>
  <div class="abs quote-outline">GET A QUOTE <svg width="14" height="14" viewBox="0 0 14 14"><circle cx="7" cy="7" r="7" fill="#10a24b"/><path d="M5.5 4l3 3-3 3" stroke="#3b3b3b" stroke-width="1.6" fill="none"/></svg></div>
  <div class="abs follow">FOLLOW US: <span class="social-dot"></span><span class="social-dot"></span><span class="social-dot"></span><span class="social-dot"></span></div>
</header>

<nav class="nav"><ul><li>HOME</li><li>ABOUT US</li><li>SERVICES</li><li>CONTACT US</li></ul></nav>

<div class="abs brand"><span class="brand-dot"></span><span class="brand-name">PEBBLEBROOK<br>PLOTS</span></div>

<section class="hero" role="img" aria-label="Photo of freshly harvested carrots lying on mulch with green tops">
  <div class="abs hero-banner">
    <h1>MORE THAN 30 YEARS<br>EXPERIANCE</h1>
    <span class="btn-quote">GET A QUOTE <svg width="20" height="20" viewBox="0 0 14 14"><rect width="14" height="14" fill="#e2581f"/><path d="M5.5 3.5l3.5 3.5-3.5 3.5" stroke="#fff" stroke-width="1.8" fill="none"/></svg></span>
  </div>
  <div class="abs dots"><span></span><span></span><span></span><span></span></div>
</section>

<section class="services">
  <div class="abs service" style="left:122px"><div class="thumb" role="img" aria-label="Garden landscape with stepping stone path" style="background:linear-gradient(135deg,#6b8a4a,#9ab36e)"></div><h3>LANDSCAPES</h3><svg class="leaf-rule" width="150" height="12"><line x1="0" y1="8" x2="150" y2="8" stroke="#9fd8b4" stroke-width="2"/><path d="M70 9c2-6 8-8 12-8-1 5-6 9-12 8z" fill="#10a24b"/></svg><p>Lorem Ipsum has been the industry's standard dummy text ever since the 1500s,when an unknown printer took</p><span class="read-more">READ MORE <svg width="14" height="14" viewBox="0 0 14 14"><circle cx="7" cy="7" r="7" fill="#3b3b3b"/><path d="M5.5 4l3 3-3 3" stroke="#fff" stroke-width="1.6" fill="none"/></svg></span></div>
  <div class="abs service" style="left:360px"><div class="thumb" role="img" aria-label="Backyard water feature pond" style="background:linear-gradient(135deg,#7a6a58,#a89c86)"></div><h3>WATERSCAPES</h3><svg class="leaf-rule" width="150" height="12"><line x1="0" y1="8" x2="150" y2="8" stroke="#9fd8b4" stroke-width="2"/><path d="M70 9c2-6 8-8 12-8-1 5-6 9-12 8z" fill="#10a24b"/></svg><p>Lorem Ipsum has been the industry's standard dummy text ever since the 1500s,when an unknown printer took</p><span class="read-more">READ MORE <svg width="14" height="14" viewBox="0 0 14 14"><circle cx="7" cy="7" r="7" fill="#3b3b3b"/><path d="M5.5 4l3 3-3 3" stroke="#fff" stroke-width="1.6" fill="none"/></svg></span></div>
  <div class="abs service" style="left:598px"><div class="thumb" role="img" aria-label="Stone patio with fire pit" style="background:linear-gradient(135deg,#8a6a4a,#b89470)"></div><h3>LIFESCAPES</h3><svg class="leaf-rule" width="150" height="12"><line x1="0" y1="8" x2="150" y2="8" stroke="#9fd8b4" stroke-width="2"/><path d="M70 9c2-6 8-8 12-8-1 5-6 9-12 8z" fill="#10a24b"/></svg><p>Lorem Ipsum has been the industry's standard dummy text ever since the 1500s,when an unknown printer took</p><span class="read-more">READ MORE <svg width="14" height="14" viewBox="0 0 14 14"><circle cx="7" cy="7" r="7" fill="#3b3b3b"/><path d="M5.5 4l3 3-3 3" stroke="#fff" stroke-width="1.6" fill="none"/></svg></span></div>
  <div class="abs service" style="left:836px"><div class="thumb" role="img" aria-label="Gardener tending flower beds" style="background:linear-gradient(135deg,#5e8a48,#c6a0a0)"></div><h3>MAINTENANCE</h3><svg class="leaf-rule" width="150" height="12"><line x1="0" y1="8" x2="150" y2="8" stroke="#9fd8b4" stroke-width="2"/><path d="M70 9c2-6 8-8 12-8-1 5-6 9-12 8z" fill="#10a24b"/></svg><p>Lorem Ipsum has been the industry's standard dummy text ever since the 1500s,when an unknown printer took</p><span class="read-more">READ MORE <svg width="14" height="14" viewBox="0 0 14 14"><circle cx="7" cy="7" r="7" fill="#3b3b3b"/><path d="M5.5 4l3 3-3 3" stroke="#fff" stroke-width="1.6" fill="none"/></svg></span></div>
</section>

<section class="welcome" role="img" aria-label="Photo of lawn grass bordered by a curving river stone path">
  <div class="abs welcome-card">
    <h2>WELCOME TO PEBBLEBROOK PLOTS</h2>
    <p>Lorem Ipsum has been the industry's standard dummy text ever since the 1500s, when an unknown printer took a galley of type and scrambled it to make a type specimen book. It has survived not only five centuries, but also the leap into electronic typesetting, remaining essentially unchanged. It was popularised in the 1960s with the release of Letraset sheets containing Lorem Ipsum passages, and more recently with desktop publishing software like Aldus PageMaker including versions of Lorem Ipsum.</p>
  </div>
</section>

<section class="projects">
  <h2 class="section-title">RECENT PROJECTS</h2>
  <svg class="leaf-rule" width="156" height="12"><line x1="0" y1="8" x2="156" y2="8" stroke="#b9d8b4" stroke-width="2"/><path d="M72 9c2-6 8-8 12-8-1 5-6 9-12 8z" fill="#10a24b"/></svg>
  <div class="abs arrow-box" style="left:67px"><svg width="12" height="14"><path d="M8 2L3 7l5 5" stroke="#555" stroke-width="2" fill="none"/></svg></div>
  <div class="abs proj" style="left:116px;background:linear-gradient(135deg,#6e5a3e,#4f7a36)" role="img" aria-label="Raised wooden garden beds"></div>
  <div class="abs proj" style="left:316px;background:linear-gradient(135deg,#8a7658,#5e6a3e)" role="img" aria-label="Stone garden patio"></div>
  <div class="abs feature-card">
    <div class="date">01 February 2016</div>
    <div class="proj-img" role="img" aria-label="Curving garden path lined with flowers" style="background:linear-gradient(135deg,#3f7d2e,#9fbf5a,#c9a0b8)"></div>
    <div class="meta"><span><svg width="14" height="12" viewBox="0 0 24 22"><path d="M12 21l-1.5-1.3C5 15 2 12 2 7.5 2 4.4 4.4 2 7.5 2c1.7 0 3.4.8 4.5 2.1C13.1 2.8 14.8 2 16.5 2 19.6 2 22 4.4 22 7.5c0 4.5-3 7.5-8.5 12.2z" fill="#3b3b3b"/></svg> 414</span><span><svg width="14" height="12" viewBox="0 0 24 20"><path d="M2 2h20v12H8l-5 5v-5H2z" fill="#3b3b3b"/></svg> 21</span></div>
  </div>
  <div class="abs proj" style="left:711px;background:linear-gradient(135deg,#9a8566,#7a8a56)" role="img" aria-label="Wooden raised planter boxes on gravel"></div>
  <div class="abs proj" style="left:898px;background:linear-gradient(135deg,#b8453a,#5e8a3a)" role="img" aria-label="Vertical living wall with red and green plants"></div>
  <div class="abs arrow-box" style="left:1083px"><svg width="12" height="14"><path d="M4 2l5 5-5 5" stroke="#555" stroke-width="2" fill="none"/></svg></div>
</section>

<section class="steps" role="img" aria-label="Photo of a lush backyard garden with plants and paving">
  <div class="abs steps-head">
    <h2 class="section-title">3 STEP PROCESS</h2>
    <svg class="leaf-rule" width="156" height="12"><line x1="0" y1="8" x2="156" y2="8" stroke="#9fd8b4" stroke-width="2"/><path d="M72 9c2-6 8-8 12-8-1 5-6 9-12 8z" fill="#10a24b"/></svg>
  </div>
  <div class="abs notch"></div>
  <div class="abs steps-panel">
    <div class="step-label" style="top:28px">Select garden size</div>
    <div class="field" style="top:66px">Either an 4' X 4', 8' X 4', or 12' X 4'<span class="addon" style="background:var(--green-dark);border:2px solid #dcd6c4"><svg width="14" height="10"><path d="M1 1h12L7 9z" fill="#fff"/></svg></span></div>
    <div class="btn-white" style="left:380px;top:66px;width:127px;height:45px">Add In Map</div>

    <div class="step-label" style="top:148px">Select Date</div>
    <div class="field" style="top:189px">12-03-2016<span class="addon" style="border-left:1px solid #c9c2ac"><svg width="16" height="16" viewBox="0 0 16 16"><rect x="1" y="3" width="14" height="12" fill="#555"/><rect x="3" y="7" width="10" height="6" fill="#dcd6c4"/><rect x="4" y="1" width="2" height="4" fill="#555"/><rect x="10" y="1" width="2" height="4" fill="#555"/></svg></span></div>
    <div class="abs calendar">
      <table>
        <tr><th colspan="7" style="font-weight:700">February 2016</th></tr>
        <tr><td>Su</td><td>Mo</td><td>Tu</td><td>We</td><td>Th</td><td>Fr</td><td>Sa</td></tr>
        <tr><td>31</td><td>1</td><td>2</td><td>3</td><td>4</td><td>5</td><td>6</td></tr>
        <tr><td>7</td><td>8</td><td>9</td><td>10</td><td>11</td><td class="sel">12</td><td>13</td></tr>
        <tr><td>14</td><td>15</td><td>16</td><td>17</td><td>18</td><td>19</td><td>20</td></tr>
        <tr><td>21</td><td>22</td><td>23</td><td>24</td><td>25</td><td>26</td><td>27</td></tr>
        <tr><td>28</td><td>29</td><td>1</td><td>2</td><td>3</td><td>4</td><td>5</td></tr>
      </table>
    </div>

    <div class="step-label" style="top:278px">Secure Payment</div>
    <div class="pay-row"><span class="radio"></span><span class="card-chip"></span><span class="card-chip"></span><span class="card-chip"></span><span class="card-chip"></span><span style="width:26px"></span><span class="radio off"></span><span class="card-chip"></span></div>
    <div class="btn-white" style="left:25px;top:380px;width:175px;height:35px;border-radius:6px">Pay $72.40</div>

    <div class="abs map" role="img" aria-label="Street map with a red pin marking the installation address"></div>
  </div>
</section>

<section class="tips">
  <h2>GARDENING <span>TIPS</span></h2>
  <div class="tip" style="top:93px">
    <div class="tip-img" role="img" aria-label="Green lawn with curved garden bed" style="background:linear-gradient(135deg,#4f8a36,#a9c76a)"></div>
    <div><h4>Lorem Ipsum has been the industry's standard.</h4><div class="date">Feb 24 2017</div><p>Lorem Ipsum has been the industry's standard dummy text ever since the 1500s, when an unknown printer took a galley of type and scrambled. <b>Read More</b></p></div>
  </div>
  <div class="tip" style="top:200px">
    <div class="tip-img" role="img" aria-label="Gardening tools and potted plants" style="background:linear-gradient(135deg,#9a7a5a,#6e9a4a)"></div>
    <div><h4>Lorem Ipsum has been the industry's standard.</h4><div class="date">Feb 24 2017</div><p>Lorem Ipsum has been the industry's standard dummy text ever since the 1500s, when an unknown printer took a galley of type and scrambled. <b>Read More</b></p></div>
  </div>
  <div class="abs newsletter"><div class="inner">
    <h3>Subcribe Newsletter</h3>
    <svg width="120" height="12" style="display:block;margin:6px auto 16px"><line x1="0" y1="8" x2="120" y2="8" stroke="#9fe0b8" stroke-width="2"/><path d="M54 9c2-6 8-8 12-8-1 5-6 9-12 8z" fill="#fff"/></svg>
    <div class="input">Name</div>
    <div class="input" style="margin-top:14px">Email Address</div>
  </div></div>
  <div class="abs submit">SUBMIT <svg width="12" height="12" viewBox="0 0 14 14"><circle cx="7" cy="7" r="7" fill="#fff"/><path d="M5.5 4l3 3-3 3" stroke="#10a24b" stroke-width="1.8" fill="none"/></svg></div>
</section>

<section class="skyline" role="img" aria-label="Silhouette scene of a park with trees, a fountain and people gardening"></section>

<footer class="footer">
  <div class="fcol" style="left:122px"><h5>WHO WE ARE</h5><ul><li>About us</li><li>Our Team</li><li>Gallery</li><li>Blog</li><li>Get a Quote</li></ul></div>
  <div class="fcol" style="left:351px"><h5>IMPORTANT LINKS</h5><ul><li>Landscapes</li><li>Waterscaps</li><li>Lifescapes</li><li>Maintenance</li><li>Other Services</li></ul></div>
  <div class="fcol" style="left:584px"><h5>CONTACT US</h5>
    <div style="margin-top:36px">
      <div class="contact-line"><svg width="16" height="16" viewBox="0 0 16 16" style="margin-top:5px"><path d="M8 1L1 8h2v7h4v-4h2v4h4V8h2z" fill="#fff"/></svg><span>123, Office Building,<br>Street, City, Country.</span></div>
      <div class="contact-line" style="margin-top:8px"><svg width="18" height="18" viewBox="0 0 24 24" style="margin-top:4px"><circle cx="12" cy="12" r="11" stroke="#fff" stroke-width="2" fill="none"/><path d="M8 7l2 3-1 1a7 7 0 0 0 4 4l1-1 3 2-1 2c-5 0-10-5-10-10z" fill="#fff"/></svg><span>123-456-7890</span></div>
      <div class="contact-line" style="margin-top:8px"><svg width="16" height="12" viewBox="0 0 16 12" style="margin-top:8px"><rect width="16" height="12" fill="#fff"/><path d="M0 0l8 7 8-7" stroke="#3b3b3b" stroke-width="1.5" fill="none"/></svg><span>PebblebrookPlots@mailvale.com</span></div>
    </div>
  </div>
  <div class="abs foot-brand"><span class="brand-dot"></span><span class="brand-name">PEBBLEBROOK<br>PLOTS</span></div>
</footer>

<div class="bottombar">
  <div class="abs" style="left:122px;top:14px">Copyright 2017. All rights reserved.</div>
  <div class="abs links"><span>Terms &amp; Condition</span><span>Privacy Policy</span></div>
  <div class="abs socials"><span class="social-dot"></span><span class="social-dot"></span><span class="social-dot"></span><span class="social-dot"></span></div>
</div>

</body>
</html>
```